Brenvik Systems PowerPoint Template

Project Title: Professional & Functional PowerPoint Template (.potx) – Brenvik Systems Rebrand

Project Overview:
Brenvik Systems has recently undergone a complete rebranding, including a new logo, website, and visual identity. We need a professional, high-end PowerPoint Template (.potx) that reflects our new look while being highly functional for everyday use.

We previously had a design created, but it was built incorrectly (static images, oversized file, no Master Slides). The goal of this project is to take our new aesthetic and build a "workable" template where layouts are controlled by Master Slides and text is easily editable.

Style & Brand Direction:
The template must be an extension of our new website: https://www.brenvik-systems.example/

Aesthetic: Modern, clean, high-tech, and "Industrial Tech."

Color Palette: Please pull the primary blues, greys, and accent colors directly from the website.

Imagery/Graphics: Use clean lines and subtle tech-inspired gradients. Avoid "clutter."

Tone: Innovative, precise, and professional.

Technical Requirements (Crucial)
Format: Must be delivered as a PowerPoint Template file (** .potx **).

Functionality: All layouts must be built using Slide Masters. Users should be able to click "New Slide" and choose from specific layouts.

Native Elements: Do NOT use full-page background images for text areas. Bullet points must use native PowerPoint list functionality (not individual text boxes).

File Size: The template must be optimized and lightweight.

Fonts: Use standard professional fonts or provide the specific web-safe equivalent used on our site (e.g., Montserrat, Open Sans, etc.).

Required Slide Layouts
Please include a minimum of 10–12 Master layouts, including:
*Title Slide (2-3 variations: Dark and Light)
*Agenda/Table of Contents
*Section Header/Divider Slides
*Standard Text/Bullet Slide
*Two-Column Text Slide
*Image + Text Layouts (Left/Right variations)
*Data/Chart Slide (Styled bar/pie charts that match the brand)
*Process/Timeline Slide (Infographic style)
*Section slide

Attachments Provided
Brand Assets (.zip): Contains our new logo in various formats.

Inspiration/Existing PPT: We have attached the previous design created by our web agency. Note: Use this for visual inspiration ONLY. Do not copy the file structure, as it is technically flawed.

Deliverables
Final .potx file.

All used icons or custom graphics in vector format (if applicable).

Instruction note on any specific fonts used.

Target Market(s)

Internal communication and external (investors, customers)

Industry/Entity Type

Semiconductor, Automotive

Requirements
Must have
• A potx file

```html
<!DOCTYPE html>
<html lang="en">
<head>
<meta charset="utf-8">
<title>Brenvik Systems – Presentation Template Overview</title>
<link href="https://fonts.googleapis.com/css2?family=Inter:wght@400;500;600;700&display=swap" rel="stylesheet">
<style>
  :root{
    --canvas:#c2c2c2;
    --white:#ffffff;
    --ink:#141414;
    --dark:#1c1d1f;
    --panel:#22252b;
    --blue:#1f45ee;
    --blue-mid:#2c5fe0;
    --blue-deep:#143a9a;
    --grey:#bdbdbd;
    --photo-a:#5d7288;
    --photo-b:#c9d3de;
  }
  *{box-sizing:border-box;margin:0;padding:0}
  html,body{width:1200px;height:374px;overflow:hidden;background:var(--canvas)}
  body{position:relative;font-family:"Inter",Arial,sans-serif;color:var(--ink)}
  .slide{position:absolute;width:281px;height:158px;background:var(--white);overflow:hidden}
  .row-1{top:22px}.row-2{top:196px}
  .col-1{left:14px}.col-2{left:311px}.col-3{left:604px}.col-4{left:901px}
  .abs{position:absolute}
  .photo{position:absolute;background:linear-gradient(135deg,var(--photo-a),var(--photo-b))}
  .photo.warm{background:linear-gradient(160deg,#2a2d33,#6b5a44 55%,#c9a56a)}
  .photo.steel{background:linear-gradient(135deg,#3d4a58,#8fa3b6 60%,#d7dee6)}
  .photo.lab{background:linear-gradient(135deg,#cfd6de,#eef1f4 60%,#b9c2cc)}
  .photo.people{background:linear-gradient(135deg,#8c96a2,#d8d3c2 60%,#c9b24a)}
  .wordmark{display:flex;align-items:center;gap:3px;font-weight:700;letter-spacing:.3px;line-height:1}
  .wordmark .mark{background:var(--blue);display:block}
  .wordmark.dark-bg{color:var(--white)}
  .wordmark.dark-bg .mark{background:var(--white)}
  .hero-title{font-weight:500;text-align:center;font-size:10.6px;line-height:1.32}
  .url{display:flex;align-items:center;gap:3px;font-size:4.6px;font-weight:500}
  .globe{width:8px;height:8px}
  .bullets{list-style:none}
  .bullets li{display:flex;align-items:flex-start;gap:5px;font-size:4.5px;line-height:1.3}
  .bullets li::before{content:"";flex:0 0 6px;height:6px;background:var(--blue);margin-top:-.5px}
  .heading{font-size:6.4px;font-weight:500}
  .small{font-size:3.2px;line-height:1.55}
  .overlay{position:absolute;background:var(--panel);color:var(--white);border-left:2px solid var(--blue);padding:8px 10px}
  .overlay h3{font-size:6px;font-weight:500;margin-bottom:6px}
  .overlay p{font-size:3.3px;line-height:1.6;font-weight:500}
</style>
</head>
<body>

<!-- Title, light -->
<section class="slide row-1 col-1">
  <svg class="abs" width="281" height="158" viewBox="0 0 281 158">
    <defs><linearGradient id="g1" x1="0" y1="0" x2="1" y2="1"><stop offset="0" stop-color="#5d7288"/><stop offset="1" stop-color="#d2dae3"/></linearGradient></defs>
    <polygon points="0,0 165,0 88,158 0,158" fill="var(--grey)"/>
    <polygon role="img" aria-label="Photo of automated robotic factory floor" points="0,0 155,0 80,158 0,158" fill="url(#g1)"/>
  </svg>
  <div class="abs wordmark" style="left:158px;top:46px;font-size:19px"><span class="mark" style="width:15px;height:15px"></span>BRENVIK</div>
  <h1 class="abs hero-title" style="left:134px;top:71px;width:140px">Engineering the Future of<br>Industrial Systems</h1>
  <div class="abs url" style="left:163px;top:132px"><svg class="globe" viewBox="0 0 10 10"><circle cx="5" cy="5" r="5" fill="var(--blue)"/><circle cx="5" cy="5" r="3" fill="none" stroke="#fff" stroke-width=".6"/><path d="M2 5h6M5 2v6" stroke="#fff" stroke-width=".6"/></svg>www.brenvik-systems.example</div>
</section>

<!-- Title, dark -->
<section class="slide row-1 col-2" style="background:var(--dark)">
  <div class="photo" role="img" aria-label="Photo of automated robotic factory floor" style="left:0;top:0;width:119px;height:158px"></div>
  <div class="abs" style="left:119px;top:0;width:4px;height:158px;background:var(--blue)"></div>
  <div class="abs wordmark dark-bg" style="left:154px;top:46px;font-size:19px"><span class="mark" style="width:15px;height:15px"></span>BRENVIK</div>
  <h1 class="abs hero-title" style="left:130px;top:73px;width:145px;color:var(--white)">Engineering the Future of<br>Industrial Systems</h1>
  <div class="abs url" style="left:162px;top:132px;color:var(--white)"><svg class="globe" viewBox="0 0 10 10"><circle cx="5" cy="5" r="5" fill="var(--blue)"/><circle cx="5" cy="5" r="3" fill="none" stroke="#fff" stroke-width=".6"/><path d="M2 5h6M5 2v6" stroke="#fff" stroke-width=".6"/></svg>www.brenvik-systems.example</div>
</section>

<!-- Agenda -->
<section class="slide row-1 col-3">
  <div class="abs wordmark" style="left:14px;top:15px;font-size:12.5px"><span class="mark" style="width:10px;height:10px"></span>BRENVIK</div>
  <h2 class="abs" style="left:14px;top:40px;font-size:6.4px;font-weight:500">AGENDA</h2>
  <ul class="abs bullets" style="left:26px;top:59px;display:grid;row-gap:7.6px">
    <li style="font-size:5.4px">About Brenvik Systems</li>
    <li style="font-size:5.4px">Technology Platform</li>
    <li style="font-size:5.4px">SiC Wafer Solutions</li>
    <li style="font-size:5.4px">Value Proposition</li>
    <li style="font-size:5.4px">Industry Applications</li>
    <li style="font-size:5.4px">Future Vision</li>
  </ul>
  <div class="abs" style="left:140px;top:0;width:5px;height:158px;background:var(--blue)"></div>
  <div class="photo people" role="img" aria-label="Photo of engineers working at computer workstations" style="left:145px;top:0;width:136px;height:158px"></div>
</section>

<!-- Image + text, right -->
<section class="slide row-1 col-4">
  <div class="photo steel" role="img" aria-label="Photo of laser processing machine over a wafer" style="left:14px;top:16px;width:115px;height:127px"></div>
  <div class="overlay" style="left:14px;top:86px;width:99px;height:58px">
    <h3>Applications &amp; Industries</h3>
    <p>Brenvik Systems technologies support industries that require high-efficiency power electronics and advanced semiconductor materials.</p>
  </div>
  <h2 class="abs heading" style="left:139px;top:24px">Advanced Laser Technology</h2>
  <p class="abs small" style="left:140px;top:38px;width:128px">Brenvik Systems develops proprietary laser-based technology designed to improve the manufacturing of advanced semiconductor materials.</p>
  <ul class="abs bullets" style="left:140px;top:61px;width:135px;display:grid;row-gap:8px">
    <li>Proprietary laser-based manufacturing technology</li>
    <li>Focus on silicon carbide (SiC) wafer processing</li>
    <li>Improves yield, quality, and efficiency in semiconductor fabrication</li>
    <li>Enables scalable production for power electronics</li>
    <li>Supports growth in EV, energy, and industrial</li>
  </ul>
</section>

<!-- Technology -->
<section class="slide row-2 col-1">
  <div class="abs" style="left:14px;top:14px;width:125px;height:129px;background:var(--blue);color:var(--white);padding:20px 10px">
    <h2 style="font-size:6.2px;font-weight:600;margin-bottom:9px">BRENVIK SYSTEMS TECHNOLOGY</h2>
    <h3 style="font-size:5.8px;font-weight:500;margin-bottom:13px">Our Technology</h3>
    <ul style="list-style:none;font-size:4.5px;line-height:1.5;display:grid;row-gap:8px">
      <li>Proprietary laser-based material processing</li>
      <li>Advanced wafer processing technology</li>
      <li>Designed for high-performance SiC materials</li>
      <li>Precision engineering for semiconductor manufacturing</li>
    </ul>
  </div>
  <div class="photo lab" role="img" aria-label="Photo of robotic inspection camera above a conveyor with a defect display" style="left:146px;top:16px;width:121px;height:51px"></div>
  <h2 class="abs" style="left:147px;top:74px;font-size:5.8px;font-weight:500">Key Benefits</h2>
  <ul class="abs bullets" style="left:152px;top:90px;display:grid;row-gap:8.5px">
    <li>Higher wafer yield and quality</li>
    <li>Reduced manufacturing waste</li>
    <li>Lower production cost</li>
    <li>Improved scalability for semiconductor</li>
  </ul>
</section>

<!-- Image + text, left -->
<section class="slide row-2 col-2">
  <div class="photo warm" role="img" aria-label="Photo of CNC laser head cutting metal with sparks" style="left:0;top:0;width:129px;height:158px"></div>
  <div class="overlay" style="left:15px;top:86px;width:98px;height:72px;padding-top:10px">
    <h3>About Brenvik Systems</h3>
    <p>Brenvik Systems develops advanced manufacturing technologies designed to improve the production of next-generation semiconductor materials.</p>
  </div>
  <h2 class="abs heading" style="left:139px;top:33px">Key Highlights</h2>
  <ul class="abs bullets" style="left:144px;top:52px;width:132px;display:grid;row-gap:8px">
    <li>Proprietary laser-based manufacturing technology</li>
    <li>Focus on silicon carbide (SiC) wafer processing</li>
    <li>Improves yield, quality, and efficiency in semiconductor fabrication</li>
    <li>Enables scalable production for power electronics</li>
    <li>Supports growth in EV, energy, and industrial</li>
  </ul>
</section>

<!-- Section header -->
<section class="slide row-2 col-3">
  <svg class="abs" width="281" height="158" viewBox="0 0 281 158">
    <defs><linearGradient id="g7" x1="0" y1="0" x2="1" y2="1"><stop offset="0" stop-color="#3a4552"/><stop offset=".6" stop-color="#8a9aab"/><stop offset="1" stop-color="#c9d2dc"/></linearGradient></defs>
    <polygon points="52,0 117,60 44,158 36,158 108,60 44,0" fill="var(--blue)"/>
    <polygon role="img" aria-label="Photo of precision machined metal part in a lathe" points="0,0 48,0 111,60 40,158 0,158" fill="url(#g7)"/>
    <path d="M198,0 H281 V4 L242,40 Q236,46 229,40 Z" fill="var(--blue)"/>
    <path d="M281,114 V158 H232 Q228,150 235,143 L272,112 Q281,106 281,114 Z" fill="var(--blue)"/>
  </svg>
  <div class="abs wordmark" style="left:146px;top:60px;font-size:18px"><span class="mark" style="width:15px;height:15px"></span>BRENVIK</div>
  <h2 class="abs" style="left:120px;top:84px;width:140px;text-align:center;font-size:11px;font-weight:500">About Brenvik Systems</h2>
  <p class="abs" style="left:110px;top:103px;width:160px;text-align:center;font-size:3.7px;line-height:1.6">Brenvik Systems develops advanced laser-based manufacturing technologies that improve efficiency and quality in semiconductor production.</p>
</section>

<!-- Data / chart -->
<section class="slide row-2 col-4">
  <div class="photo lab" role="img" aria-label="Photo of technician in cleanroom suit loading wafers into equipment" style="left:14px;top:19px;width:105px;height:120px"></div>
  <h2 class="abs heading" style="left:131px;top:33px">Manufacturing Performance Improvement</h2>
  <p class="abs small" style="left:131px;top:45px;width:135px">Brenvik Systems technology improves semiconductor wafer manufacturing by increasing efficiency and reducing material waste.</p>
  <div class="abs" style="left:132px;top:68px;font-size:4.5px;display:grid;grid-template-columns:53px auto;row-gap:7.5px;align-items:center">
    <span>Wafer Yield</span><span style="display:block;width:78px;height:9px;background:var(--blue-deep);color:#fff;font-size:2.4px;text-align:right;padding:3px 3px 0 0">35%</span>
    <span>Process Efficiency</span><span style="display:block;width:61px;height:9px;background:#1a4ab8;color:#fff;font-size:2.4px;text-align:right;padding:3px 3px 0 0">30%</span>
    <span>Material Utilization</span><span style="display:block;width:46px;height:9px;background:var(--blue-mid);color:#fff;font-size:2.4px;text-align:right;padding:3px 3px 0 0">25%</span>
    <span>Production Scalability</span><span style="display:block;width:34px;height:9px;background:#3b77ee;color:#fff;font-size:2.4px;text-align:right;padding:3px 3px 0 0">20%</span>
  </div>
</section>

</body>
</html>
```